Mark Tolvane actor business cards

I need unique and interesting business cards that have my headshot photo, my name, tagline/position/skills, contact info, preferred pronouns (he, him, his), and social media handles. These need to be memorable networking tools to hand out at events that stand out. I am an actor that works in theatre, film, and TV and usually play darker dramatic roles, though it doesn't have to necessarily need to be reflected in the design, but I am not a light, comedic actor. In my email tagline, My position/skills are "Actor, storyteller, theatre maker."

Target Market(s)

Casting directors, film and television community, theatre community.

Industry/Entity Type

Performing Art

Contact Information for Business Card

Mark Tolvane. Pronouns: he, him, his. Contact info: (555)-318-7064, Marktolvane.example, marktolvane@postbox.example. Talent representation: Kirwood Talent Agency. Social Media: Facebook page, twitter and instagram: @MarkTolvanePlays. Company Member of Harbin Theatre Company.

Font styles to use
Serif
Decorative

Colors

Designer to choose colors to be used in the design.

Requirements
Must have
• Headshot photo, name, tagline, preferred pronouns, contact info, Social media handle, talent agency logo, harbin theatre company logo. Both logos should be smaller than my name. Under or near Harbin logo, it should say "Company Member"
Nice to have
• I would like to have the photo, my name, tagline, and maybe pronouns on one side, and all contact info, and social media, and talent agency logo on the other. I would like the style to reflect my type which is a little more serious and somewhat darker, and definitely not comedic.
Should not have
• No extraneous theatre lights, camera, or film, etc. clip art or photos. Use solid backgrounds or photos provided.

```html
<!DOCTYPE html>
<html lang="en">
<head>
<meta charset="utf-8">
<title>Mark Tolvane – Business Cards</title>
<link rel="stylesheet" href="https://fonts.googleapis.com/css2?family=Fondamento&family=Lato:wght@400&family=Arimo:wght@400&display=swap">
<style>
  :root {
    --stage: #1e1e1e;
    --card-front: #ffffff;
    --card-back: #0a9bec;
    --ink: #111111;
    --accent: #1a8db5;
    --portrait-dark: #241815;
    --portrait-warm: #6b4f45;
    --rule: #0d4d73;
  }
  * { margin: 0; padding: 0; box-sizing: border-box; }
  html, body { width: 1200px; height: 900px; overflow: hidden; background: var(--stage); }
  .stage { position: relative; width: 1200px; height: 900px; }

  .card {
    position: absolute; top: 306px; width: 440px; height: 271px;
    border-radius: 10px; box-shadow: 2px 3px 5px rgba(0,0,0,.55);
  }
  .card--front { left: 149px; background: var(--card-front); }
  .card--back { left: 608px; background: var(--card-back); }

  .agency-mark {
    position: absolute; font-family: "Fondamento", serif; color: var(--ink);
    font-size: 30px; line-height: 32px;
  }
  .card--front .agency-mark { left: 26px; top: 40px; width: 190px; }
  .card--back .agency-mark { left: 0; width: 440px; top: 48px; text-align: center; }

  .name { position: absolute; left: 24px; top: 150px; font-family: "Fondamento", serif; font-size: 22px; color: var(--ink); }
  .tagline { position: absolute; left: 25px; top: 178px; font-family: "Lato", sans-serif; font-size: 13px; color: var(--accent); }
  .pronouns { position: absolute; left: 24px; top: 212px; font-family: "Fondamento", serif; font-size: 26px; color: var(--ink); }

  .headshot {
    position: absolute; left: 219px; top: 37px; width: 198px; height: 198px; border-radius: 50%;
    background: radial-gradient(circle at 52% 45%, var(--portrait-warm) 0%, var(--portrait-dark) 62%);
    border: 1px solid #000;
  }

  .icon-row { position: absolute; left: 152px; width: 136px; height: 16px; display: flex; align-items: center; gap: 4px; }
  .icon-row::before, .icon-row::after { content: ""; flex: 1; height: 1px; background: var(--rule); }
  .icon-row--contact { top: 130px; }
  .icon-row--social { top: 211px; }
  .icon-row svg { display: block; }

  .contact { position: absolute; left: 0; width: 440px; top: 154px; text-align: center; font-family: "Arimo", sans-serif; font-size: 13px; line-height: 16px; color: var(--ink); list-style: none; }
  .handle { position: absolute; left: 0; width: 440px; top: 235px; text-align: center; font-family: "Arimo", sans-serif; font-size: 13px; color: var(--ink); }
</style>
</head>
<body>
<main class="stage">
  <section class="card card--front">
    <p class="agency-mark">Kirwood Talent Agency</p>
    <h1 class="name">Mark Tolvane</h1>
    <p class="tagline">Actor, Storyteller, Theatre Maker</p>
    <p class="pronouns">He, Him, His</p>
    <div class="headshot" role="img" aria-label="Headshot portrait of Mark Tolvane"></div>
  </section>

  <section class="card card--back">
    <p class="agency-mark">Kirwood Talent Agency</p>

    <div class="icon-row icon-row--contact">
      <svg width="16" height="16" viewBox="0 0 16 16" aria-label="phone"><circle cx="8" cy="8" r="7.5" fill="#111"/><path d="M5.2 4.2l1.5-.3.8 1.9-1 .8c.5 1.2 1.3 2 2.5 2.5l.8-1 1.9.8-.3 1.5c-3.4.2-6.4-2.8-6.2-6.2z" fill="#0a9bec"/></svg>
      <svg width="16" height="16" viewBox="0 0 16 16" aria-label="email"><circle cx="8" cy="8" r="7.5" fill="#111"/><rect x="4.3" y="5.3" width="7.4" height="5.4" fill="#0a9bec"/><path d="M4.3 5.3L8 8.3l3.7-3" fill="none" stroke="#111" stroke-width=".9"/></svg>
      <svg width="16" height="16" viewBox="0 0 16 16" aria-label="website"><circle cx="8" cy="8" r="7.5" fill="#111"/><circle cx="8" cy="8" r="3.8" fill="none" stroke="#0a9bec" stroke-width="1"/><path d="M4.2 8h7.6M8 4.2v7.6" stroke="#0a9bec" stroke-width=".8"/></svg>
    </div>

    <ul class="contact">
      <li>555-318-7064</li>
      <li>marktolvane@postbox.example</li>
      <li>www.Marktolvane.example</li>
    </ul>

    <div class="icon-row icon-row--social" aria-label="social profiles">
      <svg width="18" height="18" viewBox="0 0 18 18"><circle cx="9" cy="9" r="8.5" fill="#111"/></svg>
      <svg width="18" height="18" viewBox="0 0 18 18"><circle cx="9" cy="9" r="8.5" fill="#111"/></svg>
      <svg width="18" height="18" viewBox="0 0 18 18"><circle cx="9" cy="9" r="8.5" fill="#111"/></svg>
    </div>

    <p class="handle">@MarkTolvanePlays</p>
  </section>
</main>
</body>
</html>
```